Brellwick Partners, LLC Stationary

Brellwick Partners, LLC is a new financial planning and consulting company. We are looking for designs on business cards, letterhead, envelopes, and anything else that would be useful. Our preference for business card design is two sided. We are looking for a professional and clean look with incorporating the logo and patriotic feel. Thank you to all who participate and good luck!

```html
<!DOCTYPE html>
<html lang="en">
<head>
<meta charset="utf-8">
<title>Brellwick Partners, LLC — Business Cards</title>
<link href="https://fonts.googleapis.com/css2?family=Arimo:wght@400;700&display=swap" rel="stylesheet">
<style>
  :root {
    --navy: #1f4577;
    --navy-dark: #17365f;
    --red: #c8202a;
    --ink: #5a5a5a;
    --paper: #ffffff;
    --backdrop: #e9e6e1;
  }
  * { box-sizing: border-box; margin: 0; padding: 0; }
  html, body { width: 1200px; height: 950px; overflow: hidden; }
  body {
    background: var(--backdrop);
    font-family: "Arimo", Arial, sans-serif;
    position: relative;
  }
  .card {
    position: absolute;
    left: 280px;
    width: 640px;
    height: 366px;
    background: var(--paper);
    box-shadow: 0 6px 22px rgba(0,0,0,.18);
    overflow: hidden;
  }
  .card--front { top: 72px; }
  .card--back { top: 510px; }

  /* front */
  .contact-block {
    position: absolute;
    right: 40px;
    top: 26px;
    width: 270px;
  }
  .person-name {
    color: var(--navy);
    font-weight: 700;
    font-size: 24px;
    line-height: 28px;
    letter-spacing: 1px;
    text-transform: uppercase;
  }
  .person-title {
    color: var(--red);
    font-size: 18px;
    line-height: 22px;
    letter-spacing: 1px;
    text-transform: uppercase;
    margin-top: 2px;
  }
  .address {
    color: var(--ink);
    font-size: 15px;
    line-height: 1.4;
    margin-top: 8px;
  }
  .contact-list { list-style: none; margin-top: 6px; }
  .contact-list li {
    display: flex;
    align-items: center;
    gap: 10px;
    color: var(--ink);
    font-size: 15px;
    line-height: 22px;
  }
  .contact-list svg { width: 13px; height: 13px; fill: var(--navy); flex: none; }

  .brand-lockup {
    position: absolute;
    left: 44px;
    bottom: 88px;
    display: flex;
    align-items: center;
    gap: 12px;
    white-space: nowrap;
  }
  .brand-mark { width: 22px; height: 22px; background: var(--red); flex: none; }
  .brand-name {
    color: var(--navy);
    font-weight: 700;
    font-size: 24px;
    line-height: 28px;
    letter-spacing: .5px;
  }
  .brand-tagline {
    position: absolute;
    left: 78px;
    bottom: 72px;
    color: var(--ink);
    font-size: 10px;
    line-height: 12px;
    letter-spacing: 1px;
    text-transform: uppercase;
    white-space: nowrap;
  }
  .band {
    position: absolute;
    left: 0; right: 0; bottom: 0;
    height: 58px;
    background: linear-gradient(180deg, var(--navy) 0%, var(--navy-dark) 100%);
  }
  .band-rule {
    position: absolute;
    left: 0; right: 0;
    bottom: 64px;
    height: 2px;
    background: var(--red);
  }

  /* back */
  .back-brand {
    position: absolute;
    left: 50%; top: 50%;
    transform: translate(-50%, -50%);
    display: flex;
    align-items: center;
    gap: 14px;
    white-space: nowrap;
  }
  .back-brand .brand-mark { width: 28px; height: 28px; }
  .back-brand .brand-name { font-size: 34px; line-height: 40px; }
  .web-vertical {
    position: absolute;
    left: 50px;
    top: 50%;
    transform: translate(-50%, -50%) rotate(90deg);
    color: var(--ink);
    font-size: 15px;
    letter-spacing: 3px;
    white-space: nowrap;
  }
</style>
</head>
<body>

<section class="card card--front" aria-label="Business card front">
  <div class="contact-block">
    <h1 class="person-name">Daniel Mercer</h1>
    <p class="person-title">CEO/Founder</p>
    <p class="address">4120 Birchwood Court<br>Juneau, Alaska 99801</p>
    <ul class="contact-list">
      <li><svg viewBox="0 0 16 16"><path d="M3.6 1.5l2.3 2.9-1.3 1.7c.9 2 2.6 3.8 4.6 4.7l1.7-1.3 2.9 2.3-1.5 2.4C6.9 13.9 2 9 1.5 3.1z"/></svg>555 214 3380</li>
      <li><svg viewBox="0 0 16 16"><rect x="4" y="1" width="8" height="4"/><rect x="1" y="6" width="14" height="6" rx="1"/><rect x="4" y="10" width="8" height="5"/></svg>555 371 8842</li>
      <li><svg viewBox="0 0 16 16"><path d="M1 3h14v10H1z M2 4l6 5 6-5"/></svg>hello@brellwick.com</li>
      <li><svg viewBox="0 0 16 16"><circle cx="8" cy="8" r="7"/></svg>www.brellwick.com</li>
    </ul>
  </div>

  <div class="brand-lockup">
    <span class="brand-mark"></span>
    <span class="brand-name">Brellwick Partners, LLC</span>
  </div>
  <p class="brand-tagline">Financial Planning and Consulting</p>

  <div class="band-rule"></div>
  <div class="band"></div>
</section>

<section class="card card--back" aria-label="Business card back">
  <p class="web-vertical">www.brellwick.com</p>
  <div class="back-brand">
    <span class="brand-mark"></span>
    <span class="brand-name">Brellwick Partners, LLC</span>
  </div>
</section>

</body>
</html>
```